International business needs business cards

Our company, DRV Ventures Inc. is in the business of supplying a range construction products with particular emphasis on CEMENT. We have developed our own brand - TORVAN SUPPLIES - with which to infiltrate the market. We are launching our brand of cement (TORVAN Type IS Cement) into the Caribbean which is unlike anything this market has ever seen. A monopoly has existed here for the past 60-odd years and the market has now opened to allow the importation of other brands and consumers are anxious and ready for change/improvement. We are very excited to be launching and want to make a great first impression. We will be conducting workshops and seminars (from government level to the hardware store owners) and we want our business card to give us the strong, confident introduction that we need.

Target Market(s)

construction; builders; engineers; home owners

Industry/Entity Type

Construction

Contact Information for Business Card

Marisol Depree
CEO
cell # 1 555 4180736
Ground floor,Lindell Plaza Suite 2734
George Town,Grand Cayman
Cayman Islands,KY1-4823
EMAIL: m.depree@drvventuresinc.example
web site drvventuresinc.example

COMPANY: skype info drv.ventures.example

second card
Yvette Brannock-Depree
CFO
CELL# 1 555 607 3941
George Town,Grand Cayman
Cayman Islands,KY1-4823
EMAIL: y.brannockdepree@drvventuresinc.example
website drvventuresinc.example

Requirements
Must have
• Business cards must display BOTH logos - DRV is the company and TORVAN is the brand.

```html
<!DOCTYPE html>
<html lang="en">
<head>
<meta charset="utf-8">
<title>DRV Ventures Inc. — Business Cards</title>
<link href="https://fonts.googleapis.com/css2?family=Arimo:wght@400;700&display=swap" rel="stylesheet">
<style>
  :root {
    --backdrop: #e6e3de;
    --card: #ffffff;
    --ink: #141414;
    --grey-text: #6e6e6e;
    --brand-red: #9e1b22;
    --band-red: #8f1a20;
    --crest-dark: #3a3a3a;
    --crest-light: #b9b9b9;
  }
  * { margin: 0; padding: 0; box-sizing: border-box; }
  html, body { width: 1200px; height: 950px; overflow: hidden; }
  body {
    background: var(--backdrop);
    font-family: "Arimo", Arial, sans-serif;
    color: var(--ink);
    position: relative;
  }
  .card {
    position: absolute;
    left: 240px;
    width: 720px;
    height: 411px;
    background: var(--card);
    box-shadow: 0 6px 18px rgba(0,0,0,0.18);
    overflow: hidden;
  }
  .card--front { top: 45px; }
  .card--back { top: 494px; }

  /* Front */
  .crest-area {
    position: absolute;
    left: 100px; top: 118px;
    width: 200px; height: 170px;
    border-radius: 50% 50% 44% 44%;
    background: radial-gradient(circle at 50% 45%, var(--crest-dark) 0%, #6a6a6a 45%, var(--crest-light) 100%);
  }
  .brand-lockup {
    position: absolute;
    display: flex;
    align-items: center;
    gap: 14px;
  }
  .brand-lockup__square {
    width: 86px; height: 86px;
    background: var(--brand-red);
    flex: none;
  }
  .brand-lockup__name {
    font-weight: 700;
    font-size: 34px;
    line-height: 1.05;
    color: var(--ink);
    width: 220px;
  }
  .card--front .brand-lockup { left: 340px; top: 160px; }

  /* Back */
  .card--back .brand-lockup { left: 110px; top: 64px; }
  .address {
    position: absolute;
    right: 40px; top: 108px;
    text-align: right;
    font-size: 17px;
    line-height: 1.45;
    color: var(--grey-text);
    font-style: normal;
  }
  .person {
    position: absolute;
    left: 40px; top: 232px;
  }
  .person__name {
    font-size: 24px;
    font-weight: 700;
    color: var(--brand-red);
  }
  .person__role {
    font-size: 16px;
    margin: 6px 0 10px;
  }
  .contact-line {
    display: flex;
    align-items: center;
    gap: 9px;
    font-size: 16px;
    color: #333;
    margin-bottom: 6px;
  }
  .contact-line svg { width: 15px; height: 15px; flex: none; }
  .web-band {
    position: absolute;
    left: 0; right: 0; bottom: 0;
    height: 62px;
  }
  .web-band svg { position: absolute; inset: 0; width: 100%; height: 100%; }
  .web-band__url {
    position: absolute;
    right: 42px; bottom: 18px;
    color: #fff;
    font-size: 17px;
    letter-spacing: 3px;
  }
</style>
</head>
<body>

<section class="card card--front">
  <div class="crest-area" role="img" aria-label="TORVAN brand crest emblem"></div>
  <div class="brand-lockup">
    <span class="brand-lockup__square"></span>
    <span class="brand-lockup__name">DRV Ventures Inc.</span>
  </div>
</section>

<section class="card card--back">
  <div class="brand-lockup">
    <span class="brand-lockup__square"></span>
    <span class="brand-lockup__name">DRV Ventures Inc.</span>
  </div>

  <address class="address">
    Ground floor<br>
    Lindell Plaza Suite 2734<br>
    George Town,Grand Cayman<br>
    Cayman Islands,KY1-4823
  </address>

  <div class="person">
    <p class="person__name">Marisol Depree</p>
    <p class="person__role">CEO</p>
    <p class="contact-line">
      <svg viewBox="0 0 16 16" aria-hidden="true"><rect x="3.5" y="1" width="9" height="14" rx="1.5" fill="none" stroke="#9e1b22" stroke-width="2"/></svg>
      1 555 4180736
    </p>
    <p class="contact-line">
      <svg viewBox="0 0 16 16" aria-hidden="true"><rect x="1" y="3" width="14" height="10" fill="#9e1b22"/><path d="M1 3 L8 9 L15 3" fill="none" stroke="#fff" stroke-width="1.4"/></svg>
      m.depree@drvventuresinc.example
    </p>
  </div>

  <div class="web-band">
    <svg viewBox="0 0 720 62" preserveAspectRatio="none" aria-hidden="true">
      <polygon points="0,50 260,14 720,0 720,62 0,62" fill="var(--band-red)"/>
    </svg>
    <span class="web-band__url">www.drvventuresinc.example</span>
  </div>
</section>

</body>
</html>
```